Marbrook Cupcakes Website

We need a new website. We make Texas-size gourmet cupcakes and cupcake jars. We want a website similar to the one KEYlane is hosting and made. They're charging too much per month. I would like to have Blu Otter host it. see the current site at: marbrookcupcakes.com

```html
<!DOCTYPE html>
<html lang="en">
<head>
<meta charset="utf-8">
<title>Marbrook Cupcakes</title>
<link rel="stylesheet" href="https://fonts.googleapis.com/css2?family=Quicksand:wght@400;500;600;700&display=swap">
<style>
:root{
  --teal:#5fc0c9;
  --teal-light:#9fdbe0;
  --teal-soft:#86d0d7;
  --brown:#3d1a10;
  --brown-dark:#361710;
  --ink:#1f1f1f;
  --grey-bg:#eeeeee;
  --white:#ffffff;
  --text-grey:#6a6a6a;
}
*{box-sizing:border-box;margin:0;padding:0}
html,body{width:1200px;height:5059px;overflow:hidden}
body{font-family:"Quicksand",sans-serif;color:var(--ink);background:var(--white)}
.page{position:relative;width:1200px;height:5059px;overflow:hidden}
.abs{position:absolute}
.wave{position:absolute;left:0;width:1200px;display:block}
.band{position:absolute;left:0;width:1200px;background:var(--teal)}
.btn{position:absolute;display:flex;align-items:center;justify-content:center;border-radius:20px;font-weight:700;font-size:13px;letter-spacing:.3px;text-transform:uppercase}
.btn-dark{background:var(--brown);color:var(--white)}
.btn-teal{background:var(--teal);color:var(--white)}
.section-title{position:absolute;left:0;width:1200px;text-align:center;font-weight:600;font-size:34px;color:var(--ink)}
.rule{position:absolute;height:3px;width:60px;background:var(--teal)}
.rule-center{left:570px}
.photo{position:absolute;overflow:hidden}
.ornament{position:absolute;background:var(--teal-soft);border-radius:4px}

/* header */
.logo-disc{position:absolute;background:var(--white);border-radius:50%;display:flex;align-items:center;justify-content:center;text-align:center;font-weight:700;color:var(--teal)}
.nav{position:absolute;top:30px;left:393px;font-size:13px;font-weight:600;color:var(--white)}
.nav a{position:absolute;white-space:nowrap;color:var(--white);text-decoration:none}
.search{position:absolute;left:752px;top:24px;width:303px;height:35px;background:var(--white);border-radius:18px;font-size:11px;color:#999;padding:11px 18px}
.hero-title{position:absolute;left:143px;top:232px;font-size:64px;font-weight:700;line-height:72px;color:var(--white)}
.hero-sub{position:absolute;left:143px;top:394px;font-size:16px;font-weight:600;color:var(--white)}
.dots{position:absolute;top:558px;left:566px;display:flex;gap:6px;align-items:center}
.dots span{width:11px;height:11px;border-radius:50%;background:var(--teal-light)}
.dots span:first-child{width:16px;height:16px;background:var(--white)}

/* gourmet carousel */
.cake-ring{position:absolute;width:216px;height:216px;border-radius:50%;border:5px solid var(--teal-light)}
.cake-ring .photo{inset:6px;border-radius:50%}
.cake-label{position:absolute;width:240px;text-align:center;font-size:17px;font-weight:600}
.arrow-btn{position:absolute;width:42px;height:42px;border-radius:50%;border:2px solid var(--teal);background:var(--white);display:flex;align-items:center;justify-content:center}
.view-chip{position:absolute;left:50%;top:50%;transform:translate(-50%,-50%);width:66px;height:66px;border-radius:50%;background:var(--teal);color:var(--white);font-weight:600;font-size:16px;display:flex;align-items:center;justify-content:center}

/* who we are */
.about-title{position:absolute;left:599px;top:1340px;font-size:34px;font-weight:600;color:var(--white)}
.about-text{position:absolute;left:599px;top:1396px;width:456px;font-size:13.5px;line-height:21px;color:var(--white);text-align:justify}
.about-text p+p{margin-top:21px}

/* gallery */
.g-tile{position:absolute;border-radius:12px;overflow:hidden}
.plus{position:absolute;width:58px;height:58px;border-radius:50%;background:var(--white);display:flex;align-items:center;justify-content:center}

/* order */
.order-title{position:absolute;left:544px;top:2868px;font-size:36px;font-weight:600;line-height:44px;color:var(--white)}
.order-sub{position:absolute;left:544px;top:2960px;font-size:19px;font-weight:600;color:var(--white)}

/* contact */
.map{position:absolute;left:143px;top:3317px;width:912px;height:314px;border-radius:10px;overflow:hidden}
.info-box{position:absolute;top:3657px;height:112px;background:var(--brown);border-radius:8px;color:var(--white);font-size:13px;font-weight:600}
.info-row{position:absolute;display:flex;align-items:center;white-space:nowrap}

/* news */
.news-bg{position:absolute;left:0;top:3861px;width:1200px;height:720px;background:var(--grey-bg)}
.news-card{position:absolute;top:4024px;width:285px;height:430px;background:var(--white);border-radius:4px;overflow:hidden}
.news-card .photo{left:0;top:0;width:285px;height:214px}
.news-card h3{position:absolute;left:15px;top:236px;width:255px;text-align:center;font-size:17px;font-weight:700;line-height:24px}
.news-card p{position:absolute;left:25px;top:298px;width:235px;text-align:center;font-size:12.5px;line-height:20px;color:var(--text-grey)}
.news-card .more{position:absolute;left:0;top:376px;width:285px;text-align:center;font-size:13px;font-weight:600;color:var(--teal)}

/* footer */
.footer{position:absolute;left:0;top:4570px;width:1200px;height:489px;background:var(--brown-dark)}
.f-head{position:absolute;font-size:19px;font-weight:600;color:var(--white)}
.f-list{position:absolute;list-style:none;font-size:13px;color:var(--white)}
.f-list li{height:24px;display:flex;align-items:center;gap:14px}
.f-contact{position:absolute;font-size:13px;color:var(--white);line-height:24px}
.news-input{position:absolute;left:495px;top:4908px;width:365px;height:38px;background:var(--white);border-radius:20px;font-size:11px;color:#555;padding:12px 26px}
.news-input .sub{position:absolute;right:3px;top:3px;width:112px;height:32px;background:var(--teal);border-radius:16px;color:var(--white);font-weight:700;font-size:11px;display:flex;align-items:center;justify-content:center}
.social{position:absolute;width:40px;height:40px;border-radius:50%;border:2px solid var(--white)}
.copy{position:absolute;left:0;top:5005px;width:1200px;text-align:center;font-size:13px;color:var(--white)}
</style>
</head>
<body>
<div class="page">

  <!-- HEADER / HERO -->
  <div class="band" style="top:0;height:622px"></div>
  <svg class="wave" style="top:620px" height="50" viewBox="0 0 1200 50" preserveAspectRatio="none" aria-hidden="true">
    <path fill="#5fc0c9" d="M0 0H1200V14Q1162 48 1125 14T1050 14T975 14T900 14T825 14T750 14T675 14T600 14T525 14T450 14T375 14T300 14T225 14T150 14T75 14T0 14Z"/>
  </svg>
  <div class="ornament" role="img" aria-label="Decorative wavy line ornament" style="left:0;top:550px;width:52px;height:70px"></div>

  <div class="logo-disc" style="left:118px;top:-28px;width:222px;height:222px;font-size:19px;line-height:24px;padding-top:20px">Marbrook<br>Cupcakes</div>

  <nav class="nav">
    <a style="left:0">Home</a>
    <a style="left:72px">Gallery</a>
    <a style="left:153px">Online Order</a>
    <a style="left:267px">Contact Us</a>
  </nav>
  <div class="abs" style="left:393px;top:0;width:38px;height:3px;background:#fff"></div>
  <div class="search">Search
    <svg class="abs" style="right:14px;top:12px" width="11" height="11" viewBox="0 0 12 12" aria-hidden="true"><circle cx="5" cy="5" r="3.8" fill="none" stroke="#5fc0c9" stroke-width="1.6"/><path d="M8 8l3 3" stroke="#5fc0c9" stroke-width="1.6"/></svg>
  </div>

  <h1 class="hero-title">The Best Cupcake<br>On The Planet</h1>
  <p class="hero-sub">We make Texas-size gourmet cupcakes and cupcake jars.</p>
  <div class="btn btn-dark" style="left:141px;top:434px;width:152px;height:36px">Online Order</div>

  <div class="abs" style="left:724px;top:76px;width:496px;height:496px;border-radius:50%;border:3px dashed #ffffff"></div>
  <div class="photo" role="img" aria-label="Photo of gourmet cupcakes with coconut pecan frosting in glass jars" style="left:744px;top:96px;width:456px;height:456px;border-radius:50%;background:radial-gradient(circle at 45% 45%,#b07a3a,#6b3a1a 55%,#3a1a0c)"></div>

  <div class="dots"><span></span><span></span><span></span><span></span></div>

  <!-- GOURMET CUPCAKES -->
  <div class="rule rule-center" style="top:748px"></div>
  <h2 class="section-title" style="top:764px">Gourmet Cupcakes and Cupcake Jars</h2>

  <div class="arrow-btn" style="left:50px;top:967px"><svg width="12" height="12" viewBox="0 0 12 12" aria-hidden="true"><path d="M8 2L4 6l4 4" fill="none" stroke="#333" stroke-width="1.6"/></svg></div>
  <div class="arrow-btn" style="left:1106px;top:967px"><svg width="12" height="12" viewBox="0 0 12 12" aria-hidden="true"><path d="M4 2l4 4-4 4" fill="none" stroke="#333" stroke-width="1.6"/></svg></div>

  <div class="cake-ring" style="left:139px;top:854px"><div class="photo" role="img" aria-label="Cupcake with coconut topping and cookie" style="background:radial-gradient(circle,#d9a66a,#8a5a2e 70%,#5a3018)"></div></div>
  <div class="cake-ring" style="left:375px;top:854px;border-color:var(--teal)"><div class="photo" role="img" aria-label="Chocolate cupcake with swirled caramel frosting" style="background:radial-gradient(circle,#c07850,#7a3a20 70%,#4a2010)"></div><div class="view-chip">View</div></div>
  <div class="cake-ring" style="left:609px;top:854px"><div class="photo" role="img" aria-label="Cupcake with white frosting and pecan" style="background:radial-gradient(circle,#f3ece2,#b08a68 70%,#5a3018)"></div></div>
  <div class="cake-ring" style="left:843px;top:854px"><div class="photo" role="img" aria-label="Chocolate cupcake with chocolate frosting" style="background:radial-gradient(circle,#7a3a20,#4a2010 70%,#8a5a3a)"></div></div>

  <div class="cake-label" style="left:127px;top:1086px">Lorem ipsum dolor</div>
  <div class="cake-label" style="left:363px;top:1086px">Lorem ipsum dolor</div>
  <div class="cake-label" style="left:597px;top:1086px">Lorem ipsum dolor</div>
  <div class="cake-label" style="left:831px;top:1086px">Lorem ipsum dolor</div>

  <!-- WHO WE ARE -->
  <svg class="wave" style="top:1196px" height="42" viewBox="0 0 1200 42" preserveAspectRatio="none" aria-hidden="true">
    <path fill="#5fc0c9" d="M0 42H1200V26Q1162 -8 1125 26T1050 26T975 26T900 26T825 26T750 26T675 26T600 26T525 26T450 26T375 26T300 26T225 26T150 26T75 26T0 26Z"/>
  </svg>
  <div class="band" style="top:1236px;height:586px"></div>
  <svg class="wave" style="top:1820px" height="48" viewBox="0 0 1200 48" preserveAspectRatio="none" aria-hidden="true">
    <path fill="#5fc0c9" d="M0 0H1200V14Q1162 48 1125 14T1050 14T975 14T900 14T825 14T750 14T675 14T600 14T525 14T450 14T375 14T300 14T225 14T150 14T75 14T0 14Z"/>
  </svg>

  <div class="ornament" role="img" aria-label="Decorative dot grid ornament" style="left:132px;top:1352px;width:92px;height:100px"></div>
  <div class="abs" style="left:220px;top:1288px;width:174px;height:174px;border-radius:50%;background:#2a1410"></div>
  <div class="abs" style="left:368px;top:1640px;width:150px;height:150px;border-radius:50%;background:#ffffff"></div>
  <div class="abs" style="left:134px;top:1326px;width:432px;height:432px;border-radius:50%;background:#ffffff"></div>
  <div class="photo" role="img" aria-label="Portrait of the bakery owner in a dark suit" style="left:142px;top:1334px;width:416px;height:416px;border-radius:50%;background:radial-gradient(circle at 50% 45%,#8a4a2c,#6a3220 70%,#4a2214)"></div>

  <div class="rule" style="left:599px;top:1324px;background:#fff"></div>
  <h2 class="about-title">Who We Are</h2>
  <div class="about-text">
    <p>Lorem ipsum dolor sit amet, consectetur adipiscing elit, sed do eiusmod tempor incididunt ut labore et dolore magna aliqua. Ut enim ad minim veniam, quis nostrud exercitation ullamco laboris nisi ut aliquip ex ea commodo consequat.</p>
    <p>Duis aute irure dolor in reprehenderit in voluptate velit esse cillum dolore eu fugiat nulla pariatur. Excepteur sint occaecat cupidatat non proident, sunt in culpa qui officia deserunt mollit anim id est laborum. Lorem ipsum dolor sit amet, consectetur adipiscing elit, sed do eiusmod tempor incididunt ut labore et dolore magna aliqua. Ut enim ad minim veniam, quis nostrud exercitation ullamco laboris nisi ut aliquip ex ea commodo consequat. Duis aute irure dolor in reprehenderit in voluptate velit esse cillum dolore eu fugiat nulla pariatur.</p>
  </div>
  <div class="btn btn-dark" style="left:599px;top:1715px;width:174px;height:35px">Online Order</div>

  <!-- GALLERY -->
  <div class="rule rule-center" style="top:1934px"></div>
  <h2 class="section-title" style="top:1950px">Gallery</h2>

  <div class="g-tile" role="img" aria-label="Lemon cupcakes with white frosting" style="left:143px;top:2029px;width:282px;height:253px;background:linear-gradient(135deg,#7a3a1c,#c8903a 55%,#e8d8a0)"></div>
  <div class="g-tile" role="img" aria-label="Red velvet cupcake with crumb topping" style="left:460px;top:2029px;width:281px;height:253px;background:linear-gradient(135deg,#6a2a14,#a04a2a 50%,#e0c8c0)"><div class="plus" style="left:111px;top:97px"><svg width="22" height="22" viewBox="0 0 22 22" aria-hidden="true"><path d="M11 3v16M3 11h16" stroke="#333" stroke-width="1.8"/></svg></div></div>
  <div class="g-tile" role="img" aria-label="Cupcake with caramel pecan topping" style="left:774px;top:2029px;width:281px;height:253px;background:linear-gradient(135deg,#5a2a14,#a0683a 55%,#d8b890)"></div>
  <div class="g-tile" role="img" aria-label="Chocolate cupcakes with white frosting and sprinkles" style="left:143px;top:2316px;width:437px;height:253px;background:linear-gradient(135deg,#e8e0d4,#8a5030 50%,#4a2010)"></div>
  <div class="g-tile" role="img" aria-label="Cookies and cream cupcake with chocolate frosting" style="left:619px;top:2316px;width:436px;height:253px;background:linear-gradient(135deg,#a06a3a,#5a2a18 50%,#2a1810)"></div>

  <div class="btn btn-teal" style="left:536px;top:2598px;width:128px;height:36px;border:2px solid #9fdbe0;font-size:12px">View More</div>

  <!-- ORDER ONLINE -->
  <svg class="wave" style="top:2708px" height="42" viewBox="0 0 1200 42" preserveAspectRatio="none" aria-hidden="true">
    <path fill="#5fc0c9" d="M0 42H1200V26Q1162 -8 1125 26T1050 26T975 26T900 26T825 26T750 26T675 26T600 26T525 26T450 26T375 26T300 26T225 26T150 26T75 26T0 26Z"/>
  </svg>
  <div class="band" style="top:2748px;height:398px"></div>
  <svg class="wave" style="top:3144px" height="48" viewBox="0 0 1200 48" preserveAspectRatio="none" aria-hidden="true">
    <path fill="#5fc0c9" d="M0 0H1200V14Q1162 48 1125 14T1050 14T975 14T900 14T825 14T750 14T675 14T600 14T525 14T450 14T375 14T300 14T225 14T150 14T75 14T0 14Z"/>
  </svg>
  <div class="photo" role="img" aria-label="Young basketball player in a red uniform leaping while holding up a cupcake" style="left:80px;top:2682px;width:400px;height:540px;border-radius:40px;background:radial-gradient(ellipse at 50% 45%,#b8303a,#7a2a24 45%,rgba(95,192,201,0) 72%)"></div>

  <div class="rule" style="left:544px;top:2846px;background:#fff"></div>
  <h2 class="order-title">Gourmet Cupcakes?<br>Order online now!</h2>
  <p class="order-sub">Order your favorite Cupcakes online at your convenience.</p>
  <div class="btn btn-dark" style="left:544px;top:3007px;width:214px;height:34px">Order Online Now</div>

  <!-- CONTACT -->
  <div class="rule rule-center" style="top:3231px"></div>
  <h2 class="section-title" style="top:3247px">Contact Us</h2>
  <div class="map" role="img" aria-label="Street map showing the bakery location with a red pin" style="background:linear-gradient(135deg,#e6ece4,#dfe6ee 50%,#e8eee2)">
    <div class="abs" style="left:442px;top:148px;width:20px;height:20px;border-radius:50% 50% 50% 0;transform:rotate(-45deg);background:#e23b32"></div>
  </div>

  <div class="info-box" style="left:143px;width:440px">
    <div class="abs" style="left:36px;top:41px;width:30px;height:30px;border-radius:50%;background:var(--teal);display:flex;align-items:center;justify-content:center">
      <svg width="14" height="14" viewBox="0 0 14 14" aria-hidden="true"><circle cx="7" cy="7" r="5.5" fill="none" stroke="#fff" stroke-width="1.4"/><path d="M7 4v3.3l2 1.4" fill="none" stroke="#fff" stroke-width="1.4"/></svg>
    </div>
    <div class="info-row" style="left:80px;top:34px">Tue - Fri</div>
    <div class="info-row" style="left:166px;top:34px">5:00 PM - 10:00 PM</div>
    <div class="info-row" style="left:80px;top:66px">Sat - Sun</div>
    <div class="info-row" style="left:166px;top:66px">12:00 PM - 10:00 PM</div>
  </div>
  <div class="info-box" style="left:615px;width:440px">
    <div class="info-row" style="left:46px;top:34px;gap:20px">
      <svg width="12" height="12" viewBox="0 0 12 12" aria-hidden="true"><path d="M2.5 1h2l1 3-1.4 1a7 7 0 0 0 3 3l1-1.4 3 1v2c0 .6-.5 1-1 1A10 10 0 0 1 1.5 2c0-.5.4-1 1-1z" fill="#5fc0c9"/></svg>+1 888 888 8888</div>
    <div class="info-row" style="left:46px;top:66px;gap:20px">
      <svg width="12" height="14" viewBox="0 0 12 14" aria-hidden="true"><path d="M6 1a4.3 4.3 0 0 0-4.3 4.3C1.7 8.5 6 13 6 13s4.3-4.5 4.3-7.7A4.3 4.3 0 0 0 6 1zm0 6a1.7 1.7 0 1 1 0-3.4A1.7 1.7 0 0 1 6 7z" fill="#5fc0c9"/></svg>123, Lorem ipsum dolor sit amet, consectetur</div>
  </div>

  <!-- LATEST NEWS -->
  <div class="news-bg"></div>
  <div class="rule rule-center" style="top:3940px"></div>
  <h2 class="section-title" style="top:3956px">Latest News</h2>

  <div class="arrow-btn" style="left:50px;top:4221px;border-color:#fff"><svg width="12" height="12" viewBox="0 0 12 12" aria-hidden="true"><path d="M8 2L4 6l4 4" fill="none" stroke="#333" stroke-width="1.6"/></svg></div>
  <div class="arrow-btn" style="left:1106px;top:4221px;border-color:#fff"><svg width="12" height="12" viewBox="0 0 12 12" aria-hidden="true"><path d="M4 2l4 4-4 4" fill="none" stroke="#333" stroke-width="1.6"/></svg></div>

  <article class="news-card" style="left:143px">
    <div class="photo" role="img" aria-label="Strawberry cupcake with white frosting" style="background:linear-gradient(135deg,#6a2a14,#b0583a 50%,#f0d8d0)"></div>
    <h3>Lorem ipsum dolor sit amet, consectetur</h3>
    <p>Lorem ipsum dolor sit amet, consectetur adipiscing elit, sed do eiusmod tempor incididunt ut labore</p>
    <div class="more">Learn More &#10140;</div>
  </article>
  <article class="news-card" style="left:458px">
    <div class="photo" role="img" aria-label="Cupcake with white swirled frosting in a glass jar" style="background:linear-gradient(135deg,#8a5a2a,#c09060 50%,#f0ebe2)"></div>
    <h3>Lorem ipsum dolor sit amet, consectetur</h3>
    <p>Lorem ipsum dolor sit amet, consectetur adipiscing elit, sed do eiusmod tempor incididunt ut labore</p>
    <div class="more">Learn More &#10140;</div>
  </article>
  <article class="news-card" style="left:770px">
    <div class="photo" role="img" aria-label="Cupcake with coconut topping and cookie" style="background:linear-gradient(135deg,#5a2a14,#b07a40 50%,#e0c090)"></div>
    <h3>Lorem ipsum dolor sit amet, consectetur</h3>
    <p>Lorem ipsum dolor sit amet, consectetur adipiscing elit, sed do eiusmod tempor incididunt ut labore</p>
    <div class="more">Learn More &#10140;</div>
  </article>

  <!-- FOOTER -->
  <svg class="wave" style="top:4532px" height="42" viewBox="0 0 1200 42" preserveAspectRatio="none" aria-hidden="true">
    <path fill="#361710" d="M0 42H1200V26Q1162 -8 1125 26T1050 26T975 26T900 26T825 26T750 26T675 26T600 26T525 26T450 26T375 26T300 26T225 26T150 26T75 26T0 26Z"/>
  </svg>
  <div class="footer"></div>

  <div class="logo-disc" style="left:202px;top:4655px;width:226px;height:226px;font-size:20px;line-height:26px">Marbrook<br>Cupcakes</div>

  <h3 class="f-head" style="left:550px;top:4668px">Quick Links</h3>
  <ul class="f-list" style="left:550px;top:4716px">
    <li>&raquo;<span>Home</span></li>
    <li>&raquo;<span>About us</span></li>
    <li>&raquo;<span>Services</span></li>
    <li>&raquo;<span>Blog</span></li>
    <li>&raquo;<span>Gallery</span></li>
    <li>&raquo;<span>Contact</span></li>
  </ul>

  <h3 class="f-head" style="left:831px;top:4668px">Contact Us</h3>
  <div class="f-contact" style="left:831px;top:4716px">
    <div style="display:flex;gap:16px"><svg width="10" height="24" viewBox="0 0 10 14" aria-hidden="true"><path d="M5 1a3.6 3.6 0 0 0-3.6 3.6C1.4 7.4 5 11 5 11s3.6-3.6 3.6-6.4A3.6 3.6 0 0 0 5 1z" fill="#5fc0c9"/></svg><span>123,Lorem ipsum dolor<br>amet, conse</span></div>
    <div style="display:flex;gap:16px;margin-top:16px"><svg width="10" height="24" viewBox="0 0 12 12" aria-hidden="true"><path d="M2.5 1h2l1 3-1.4 1a7 7 0 0 0 3 3l1-1.4 3 1v2c0 .6-.5 1-1 1A10 10 0 0 1 1.5 2c0-.5.4-1 1-1z" fill="#5fc0c9"/></svg><span>+1 888 888 8888</span></div>
    <div style="display:flex;gap:16px;margin-top:24px"><svg width="12" height="24" viewBox="0 0 12 12" aria-hidden="true"><path d="M1 3h10v6H1z" fill="#5fc0c9"/><path d="M1 3l5 3.5L11 3" fill="none" stroke="#361710" stroke-width="1"/></svg><span>info@companyname.com</span></div>
  </div>

  <div class="f-head" style="left:187px;top:4913px;font-size:18px">Subscribe To Our Newsletter</div>
  <div class="news-input">Email address<div class="sub">SUBSCRIBE</div></div>

  <div class="social" role="img" aria-label="Social link" style="left:926px;top:4906px;background:var(--teal)"></div>
  <div class="social" role="img" aria-label="Social link" style="left:976px;top:4906px"></div>

  <p class="copy">&copy; Copyrights 2025 | All Rights Reserved</p>
</div>
</body>
</html>
```